Business Card - Business Consultancy

Newly Established Company, specializing in Business Consultancy, Human Resource Management, Talent Acquisition and Payroll Solutions.

We need a Business card design which portrays "elegance" and a very sleek yet business-like design. We would like a nice blue trimming (which goes well with the logo) to separate the content of the business card at the top. We would also like to see the design using the color silver either as a background or incorporated into it.

The final design should be a Business card which has colors matching the logo; a nice font; the above-mentioned specifics that adheres to the theme of "a stylish and professional business"

FYI: please do not have too fanciful designs.

Industry/Entity Type

Business Consultant

Contact Information for Business Card

Darren Lim
Business Development Director
Arbor Talent Consulting Private Limited
27 Wexley Street, #05-03B
Harbourgate Trade Building
Singapore 059317
Mobile : (+65) 98354417
Email : dlim@arbortalent-advisory.com
Alternative : arbortalentadvisory@mailbox-example.com

Requirements
Must have
• Nice Blue Trimming matching Logo which separates content, see attached
• Design incorporates either a silver background or the use of the color silver
Should not have
• No Fanciful Designs
• No Childish Designs
• No Overly Complicated Designs

```html
<!DOCTYPE html>
<html lang="en">
<head>
<meta charset="utf-8">
<title>Arbor Talent Consulting – Business Card</title>
<link rel="stylesheet" href="https://fonts.googleapis.com/css2?family=Open+Sans:wght@400;600;700;800&display=swap">
<style>
  :root {
    --stage: #000000;
    --card-silver: #f3f3f3;
    --brand-green: #7fc128;
    --brand-blue: #1a7bc4;
    --ink: #2b2b2b;
    --ink-soft: #3a3a3a;
    --rule: #dcdcdc;
    --white: #ffffff;
  }
  * { margin: 0; padding: 0; box-sizing: border-box; }
  html, body {
    width: 1200px; height: 900px; overflow: hidden;
    background: var(--stage);
    font-family: "Open Sans", Arial, sans-serif;
  }
  .stage { position: relative; width: 1200px; height: 900px; }

  .card { position: absolute; top: 200px; width: 310px; height: 502px; overflow: hidden; }
  .card-front {
    left: 265px; background: var(--card-silver);
    border-radius: 66px 0 66px 0;
  }
  .card-back {
    left: 641px; background: var(--brand-green);
    border-radius: 0 66px 0 66px;
  }

  .brand-mark {
    position: absolute; left: 92px; top: 52px;
    width: 62px; height: 62px; border-radius: 50%;
    background: var(--brand-blue);
  }
  .brand-name {
    position: absolute; right: 17px; top: 60px;
    text-align: right; color: var(--ink);
    font-weight: 700; font-size: 19px; line-height: 23px;
  }
  .brand-rule {
    position: absolute; left: 85px; top: 142px;
    width: 98px; height: 1px; background: var(--rule);
  }

  .contact { position: absolute; left: 27px; right: 12px; top: 284px; color: var(--ink-soft); }
  .person-name {
    color: var(--brand-green); font-weight: 700; font-size: 17px;
    line-height: 22px; text-transform: uppercase;
  }
  .person-title { color: var(--brand-blue); font-size: 13.5px; line-height: 22px; }
  .address { margin-top: 14px; font-size: 13px; line-height: 15px; }
  .lines { margin-top: 22px; list-style: none; font-size: 13px; line-height: 18.5px; }
  .lines li { display: flex; align-items: center; white-space: nowrap; }
  .lines .email-alt { font-size: 10.6px; }
  .lines svg { width: 10px; height: 10px; margin-right: 6px; flex: none; }

  .back-name {
    position: absolute; left: 0; right: 0; top: 180px;
    text-align: center; color: var(--white);
    font-weight: 800; font-size: 38px; line-height: 46px;
  }
  .services {
    position: absolute; left: 0; right: 0; top: 398px;
    list-style: none; text-align: center; color: var(--white);
    font-size: 18px; line-height: 25px;
    padding-left: 18px;
  }
</style>
</head>
<body>
<main class="stage">
  <section class="card card-front">
    <div class="brand-mark"></div>
    <div class="brand-name">Arbor Talent<br>Consulting</div>
    <div class="brand-rule"></div>

    <div class="contact">
      <h1 class="person-name">Darren Lim</h1>
      <p class="person-title">Business Development Director</p>
      <p class="address">27 Wexley Street, #05-03B<br>Harbourgate Trade Building<br>Singapore 059317</p>
      <ul class="lines">
        <li>
          <svg viewBox="0 0 10 10" aria-hidden="true"><path d="M1 4 Q5 0 9 4 L7.5 5 L6.5 3.8 L3.5 3.8 L2.5 5 Z M2.5 5.5 H7.5 L8.5 9 H1.5 Z" fill="#7fc128"/></svg>
          (+65) 98354417
        </li>
        <li>
          <svg viewBox="0 0 10 10" aria-hidden="true"><rect x="0.5" y="2" width="9" height="6.5" fill="#7fc128"/><path d="M0.5 2 L5 5.6 L9.5 2" stroke="#f3f3f3" stroke-width="0.9" fill="none"/></svg>
          Email : dlim@arbortalent-advisory.com
        </li>
        <li class="email-alt">
          <svg viewBox="0 0 10 10" aria-hidden="true"><rect x="0.5" y="2" width="9" height="6.5" fill="#7fc128"/><path d="M0.5 2 L5 5.6 L9.5 2" stroke="#f3f3f3" stroke-width="0.9" fill="none"/></svg>
          Email : arbortalentadvisory@mailbox-example.com
        </li>
      </ul>
    </div>
  </section>

  <section class="card card-back">
    <div class="back-name">Arbor Talent<br>Consulting</div>
    <ul class="services">
      <li>Recruitment</li>
      <li>HR Solutions</li>
      <li>Business Consultancy</li>
    </ul>
  </section>
</main>
</body>
</html>
```